Hurricane Damage Public Adjuster Billboard

I have created several projects with you and have several great designs. I need to format them into a Billboard for upcoming Hurricane Season. Need done in a month. Im also in process of getting an eye catching and easy to remember 800# Vanity phone number like Call 800-Stormsafe or 800- Need Fix? My included past Craft Huddle projects will give you an idea of what colors, schemes, and designs I gravitate towards. 3 past Design projects were 1) 2 Logos where I picked the 1st place and the 2nd place and 2) Index Card where I picked the winner as the Index Card and the 2nd place as a Post Card. Point is, I will pick and pay for 2 winners if they're good. This should help to sweeten the pot. Also, please look at my website for ideas that I like:

www.TheClaimKeeperGroup.com
I want people to feel that I am the best and highest. Level.

I've been getting a lot of quick half effort designs basically cut & pasting my previous projects. Please don't rush and take your time to be creative. A an example, my Biggest Competitor is Vesta Public Adjusting. Their colors are Black and Gold while mine are Blue, White, and Black with a highlight of Orange if possible. I JUST imported a picture of their BillBoard. I need mine better and BLOW AWAY THEIRS. Terms like "Don't be Victimized Twice ?, Don't let the Hurricane Ruin your Life?". "Get Fairly Paid & Move On" "Our Clients Claims are VIP?
Updates

I'm getting a lot of quick half effort ones. I'd rather you take your time and really put some thoughts and effort into it. My Biggest Competitor is Vesta Public Adjusting. They have black & gold colors, while I have Blue, Black, and white.

It needs to blow theirs away. I have imported their Billboard for comparative purposes.

Guy's,
I'll make it easier for you in what I'm looking for. Please look at the Vesta Billboard picture attached.

1) Put my "Blue Shield" to the left, replacing their logo
2) change color patterns from their (Black, Gold, White) to my color schemes of (Black, Blue, White)
3) I want to see my name where their is:

THE
Claim Keeper's Group
EXPERT & LOCAL Public Adjusters
"FOR THE POLICYHOLDER!!"

4) to the right, add the A+Rated logo and QRS+ Accredited logo, 5 Star Zorbix Rated logo, 5 Start PORCHLINE Highly Rated logo, etc..

5) the right side is where you can be creative as I will not have a picture of me there.

"20+ Years of Experience, Recovering Millions for our VIP Clients"

"Your Best, Locally-Based Private Adjuster & Advocate'
"FOR THE POLICYHOLDER!!"

"Don't be victimized Twice!!"

"Don't let the Hurricane Ruin Your Life!!"

This should really help. Also, refer to my website, maybe a couple testimonial fillers?

Thanks all,

marcus@TheClaimKeeperGroup.com

Just imported a few awards that would look great to the right side with all the other 5 Star Ratings and accolades.
This right section could be titled like zmy Website:

5 Star Reviews, Ratings & Awards:
4-5 Logos underneath?

Target Market(s)

Coastal place where a Hurricane 🌀 🌀 Hits

Industry/Entity Type

Hurricane Public Insurance Adjuster

Font styles to use
Sans Serif
Other font styles liked:
• Zurich fonts

Colors
0054AA
0677BA
7BADD7
CADEEF
E8F1F8
EE7325
F08F49
F5BC92
FAE3D3
FDF4ED

Requirements
Must have
• Use my past project logos, colors, and schemes to create eye grabbing BillBoard
Nice to have
Should not have
• Not be too busy, must be Easy to Read, Eye Catchy

```html
<!DOCTYPE html>
<html lang="en">
<head>
<meta charset="utf-8">
<title>The Claim Keeper's Group – Billboard</title>
<link rel="stylesheet" href="https://fonts.googleapis.com/css2?family=Playfair+Display:wght@800&family=Poppins:wght@500;600;700;800&display=swap">
<style>
  :root{
    --navy:#061a3a;
    --navy-deep:#020b1d;
    --black:#000;
    --cyan:#16b4ee;
    --blue:#0054aa;
    --blue-mid:#0677ba;
    --sky:#7badd7;
    --orange:#ee7325;
    --white:#fff;
    --ink:#222;
    --red:#e2342b;
    --gold:#f4b400;
  }
  *{margin:0;padding:0;box-sizing:border-box}
  html,body{width:1076px;height:1200px;overflow:hidden;background:var(--white)}
  body{font-family:"Poppins",sans-serif;position:relative}
  .billboard{position:absolute;left:38px;top:454px;width:1000px;height:292px;overflow:hidden;box-shadow:0 6px 18px rgba(0,0,0,.18)}
  .billboard-shapes{position:absolute;inset:0;width:1000px;height:292px}
  .abs{position:absolute}
  .brand-mark{left:22px;top:22px;width:112px;height:120px;display:flex;flex-direction:column;align-items:center;justify-content:center;gap:6px;text-align:center;
    font-weight:700;font-size:17px;line-height:1.1;color:var(--cyan)}
  .brand-mark .dot{width:22px;height:22px;border-radius:50%;background:var(--cyan)}
  .name-top{left:150px;top:8px;width:470px;text-align:center;font-family:"Playfair Display",serif;font-weight:800;font-size:36px;color:var(--cyan);letter-spacing:.5px;line-height:1}
  .name-main{left:170px;top:46px;width:430px;display:flex;align-items:center;gap:14px}
  .name-main .rule{flex:1;height:2px;background:var(--cyan)}
  .name-main span{font-weight:700;font-size:40px;color:var(--white);line-height:1}
  .tagline{left:150px;top:92px;width:470px;text-align:center;font-weight:800;font-size:29px;color:var(--orange);line-height:1}
  .thin-rule{left:196px;top:135px;width:380px;height:1px;background:var(--cyan)}
  .slogan{left:18px;top:146px;font-weight:600;font-size:23px;color:var(--white)}
  .call{left:14px;top:200px;display:flex;align-items:baseline;gap:14px;font-weight:700;font-size:29px;line-height:1}
  .call .label{color:var(--cyan)}
  .call .phone{color:var(--white)}
  .web{left:17px;top:245px;font-weight:600;font-size:17px;letter-spacing:4.2px;color:var(--white)}
  .web b{color:var(--orange);font-weight:700}
  .experience{left:724px;top:12px;display:flex;align-items:flex-start;gap:2px}
  .experience .num{font-weight:800;font-size:50px;color:var(--blue);line-height:.95;letter-spacing:-2px}
  .experience .plus{font-weight:800;font-size:16px;color:var(--blue);line-height:1}
  .experience .years{font-weight:600;font-size:15px;color:var(--blue);line-height:1.05;margin-top:10px}
  .recover{left:724px;top:60px;font-weight:800;font-size:19.5px;color:var(--orange);line-height:1.1}
  .local{left:744px;top:118px;font-weight:600;font-size:20.5px;line-height:1.2;color:var(--white)}
  .local .accent{color:var(--cyan);font-weight:700}
  .ratings{left:655px;top:228px;width:340px;display:flex;align-items:center;justify-content:space-between;padding-right:12px}
  .rating-a{text-align:center;color:var(--red);font-weight:600;font-size:16px;line-height:1}
  .rating-a small{display:block;font-family:"Playfair Display",serif;font-weight:800;font-size:6px;color:var(--ink);line-height:1.2;margin-top:2px}
  .rating-z{text-align:center;font-weight:600;font-size:17px;color:var(--blue);line-height:1}
  .stars{display:block;margin-top:1px}
  .rating-p{font-weight:600;font-size:13px;color:var(--blue)}
  .badge-plain{width:68px;height:26px;border-radius:4px;background:var(--blue-mid)}
</style>
</head>
<body>
<section class="billboard">
  <svg class="billboard-shapes" viewBox="0 0 1000 292" aria-hidden="true">
    <defs>
      <linearGradient id="stormSky" x1="0" y1="0" x2="1" y2="1">
        <stop offset="0" stop-color="#0a2550"/>
        <stop offset=".55" stop-color="#061a3a"/>
        <stop offset="1" stop-color="#020b1d"/>
      </linearGradient>
      <radialGradient id="awardFill" cx=".5" cy=".45" r=".55">
        <stop offset="0" stop-color="#b8c6d8"/>
        <stop offset=".55" stop-color="#7a1f2b"/>
        <stop offset="1" stop-color="#0b1a33"/>
      </radialGradient>
    </defs>
    <rect width="1000" height="292" fill="#fff"/>
    <rect x="660" y="112" width="340" height="100" fill="var(--blue)"/>
    <path d="M0 0 H718 C706 90 712 170 660 222 C620 262 575 284 530 292 H0 Z" fill="var(--cyan)"/>
    <path d="M0 0 H700 C688 90 692 160 648 212 C610 258 570 280 520 292 H0 Z" fill="url(#stormSky)"/>
    <path d="M0 196 H660 C620 250 574 280 520 292 H0 Z" fill="var(--black)"/>
    <circle cx="676" cy="160" r="54" fill="var(--navy)" stroke="var(--cyan)" stroke-width="4"/>
    <circle cx="676" cy="160" r="38" fill="url(#awardFill)" role="img" aria-label="2022 crystal award trophy"/>
  </svg>

  <div class="abs brand-mark"><span class="dot"></span>Claim<br>Keeper's<br>Group</div>

  <h1 class="abs name-top">THE CLAIM KEEPER'S</h1>
  <div class="abs name-main"><i class="rule"></i><span>GROUP</span><i class="rule"></i></div>
  <p class="abs tagline">FOR THE POLICYHOLDER!!</p>
  <div class="abs thin-rule"></div>
  <p class="abs slogan">Don't let the Hurricane Ruin Your Life!!</p>

  <p class="abs call"><span class="label">CALL NOW</span><span class="phone">850-555-0142</span></p>
  <p class="abs web">www.<b>theclaimkeepergroup</b>.com</p>

  <div class="abs experience"><span class="num">20</span><span class="plus">+</span><span class="years">YEARS OF<br>EXPERIENCE</span></div>
  <p class="abs recover">RECOVERING MILLIONS<br>FOR OUR VIP CLIENTS</p>
  <p class="abs local">Your Best, Locally<br>Based Private<br><span class="accent">Adjuster &amp; Advocate</span></p>

  <div class="abs ratings">
    <div class="rating-a">A+ Rating<small>Highest Rating For<br>Public Insurance Adjusters<br>Source: AdjusterIndex</small></div>
    <div class="rating-z">Zorbix
      <svg class="stars" width="44" height="8" viewBox="0 0 55 10" aria-label="five stars">
        <g fill="var(--gold)">
          <polygon points="5,0 6.2,3.6 10,3.6 7,5.9 8.1,9.5 5,7.3 1.9,9.5 3,5.9 0,3.6 3.8,3.6"/>
          <polygon transform="translate(11 0)" points="5,0 6.2,3.6 10,3.6 7,5.9 8.1,9.5 5,7.3 1.9,9.5 3,5.9 0,3.6 3.8,3.6"/>
          <polygon transform="translate(22 0)" points="5,0 6.2,3.6 10,3.6 7,5.9 8.1,9.5 5,7.3 1.9,9.5 3,5.9 0,3.6 3.8,3.6"/>
          <polygon transform="translate(33 0)" points="5,0 6.2,3.6 10,3.6 7,5.9 8.1,9.5 5,7.3 1.9,9.5 3,5.9 0,3.6 3.8,3.6"/>
          <polygon transform="translate(44 0)" points="5,0 6.2,3.6 10,3.6 7,5.9 8.1,9.5 5,7.3 1.9,9.5 3,5.9 0,3.6 3.8,3.6"/>
        </g>
      </svg>
    </div>
    <div class="rating-p">PORCHLINE</div>
    <div class="badge-plain" role="img" aria-label="accreditation badge"></div>
  </div>
</section>
</body>
</html>
```